Blue Harbor Mortgages Social Media Campaign

I need social media campaign banners. Facebook and Instagram.
I would like them to incorporate local photos, my photo and my logo. I have some sample files of previous campaigns and I have a color scheme associated with my brand. My business operates in St. John's Newfoundland.

Target Market(s)

Home Buyers, Home Owners

Industry/Entity Type

Mortgage Brokering

Logo Text

Blue Harbor Mortgages

Logo styles of interest
Lettermark Logo
Font styles to use
Other font styles liked:
• Times New Roman, I'm open to suggestion

Colors
0054AA
0677BA
7BADD7
CADEEF
E8F1F8
EE7325
F08F49
F5BC92
FAE3D3
FDF4ED

Requirements
Must have
• My name, photo, contact info, slogan
Nice to have
• We can discuss slogans to use, I can provide some suggestions.

```html
<!DOCTYPE html>
<html lang="en">
<head>
<meta charset="utf-8">
<title>Blue Harbor Mortgages – Social Posts</title>
<link href="https://fonts.googleapis.com/css2?family=Montserrat:wght@400;500;600;700;800&display=swap" rel="stylesheet">
<style>
  :root{
    --stage:#d6d6d6;
    --navy:#0b1a5c;
    --orange:#ff4100;
    --white:#ffffff;
    --btn:#0a49b8;
    --caption:#555555;
    --sky:#3f7fd8;
    --hill:#4f8a36;
    --rock:#8a8a6e;
  }
  *{box-sizing:border-box;margin:0;padding:0}
  html,body{width:1200px;height:854px;overflow:hidden}
  body{background:var(--stage);font-family:"Montserrat",sans-serif;position:relative}

  .post{position:absolute;overflow:hidden;background:var(--navy);transform-origin:0 0;transform:scale(.569)}
  .post--square{left:113px;top:256px;width:604px;height:604px}
  .post--wide{left:507px;top:256px;width:1073px;height:602px}
  .post svg.art{position:absolute;left:0;top:0}

  .brand{position:absolute;color:var(--white);text-align:center;font-weight:800;letter-spacing:.2px;line-height:1}
  .brand__tagline{display:flex;align-items:center;gap:6px;justify-content:center;font-weight:700;margin-top:4px}
  .brand__tagline::before,.brand__tagline::after{content:"";height:2px;flex:1;background:var(--white)}

  .headline{position:absolute;font-weight:800;line-height:1.08;text-transform:uppercase}
  .headline__lead{color:var(--white);display:block}
  .headline__accent{color:var(--orange);display:block}
  .rule{position:absolute;height:3px;background:var(--white)}

  .pitch{position:absolute;color:var(--white);font-weight:400;line-height:1.35;white-space:nowrap}
  .pitch b{font-weight:700}
  .call{position:absolute;color:var(--orange);font-weight:800}
  .phone{position:absolute;color:var(--white);font-weight:800;display:flex;align-items:center;gap:10px;letter-spacing:.5px;white-space:nowrap}

  .cta{position:absolute;background:var(--btn);color:var(--white);font-weight:500;display:flex;align-items:center;justify-content:center;gap:4px;border-radius:3px;white-space:nowrap}
  .cta span{color:var(--orange);font-weight:800}

  .footer{position:absolute;left:0;background:var(--orange);color:var(--white);display:flex;align-items:center;font-weight:400;white-space:nowrap}
  .footer__item{display:inline-flex;align-items:center;gap:4px}
  .footer__item b{font-weight:700}
  .footer__icon{display:inline-block;border:2px solid var(--white);border-radius:50%;opacity:.85;flex:none}
  .footer__sep{font-weight:700;margin:0 10px}

  .caption{position:absolute;color:var(--caption);font-weight:600;font-size:18px;text-align:center}
</style>
</head>
<body>

<section class="post post--square">
  <svg class="art" width="604" height="604" viewBox="0 0 604 604">
    <defs>
      <linearGradient id="sq-scene" x1="0" y1="0" x2="0" y2="1">
        <stop offset="0" stop-color="#3f7fd8"/><stop offset=".35" stop-color="#8a8a6e"/><stop offset="1" stop-color="#4f8a36"/>
      </linearGradient>
      <linearGradient id="sq-person" x1="0" y1="0" x2="0" y2="1">
        <stop offset="0" stop-color="#c99563"/><stop offset=".55" stop-color="#d8a37a"/><stop offset=".7" stop-color="#16204a"/><stop offset="1" stop-color="#101a40"/>
      </linearGradient>
      <linearGradient id="sq-house" x1="0" y1="0" x2="1" y2="1">
        <stop offset="0" stop-color="#eef0f2"/><stop offset="1" stop-color="#c7a58c"/>
      </linearGradient>
    </defs>
    <path role="img" aria-label="Hillside of colourful houses under blue sky in St. John's" d="M210,0 L604,0 L604,190 Q560,210 520,150 Q420,120 300,130 Q225,90 210,0 Z" fill="url(#sq-scene)"/>
    <path d="M0,0 L210,0 Q212,95 232,140 L150,192 Q112,210 80,190 L0,145 Z" fill="#ff4100"/>
    <polygon points="318,106 401,152 401,245 318,291 236,245 236,152" fill="#b8c4de" opacity=".6"/>
    <polygon role="img" aria-label="Hands holding a small model house and keys" points="318,114 394,156 394,241 318,283 243,241 243,156" fill="url(#sq-house)"/>
    <path role="img" aria-label="Portrait of the mortgage broker" d="M340,560 Q340,360 410,260 Q470,140 540,140 Q604,150 604,250 L604,560 Z" fill="url(#sq-person)"/>
  </svg>

  <div class="brand" style="left:28px;top:40px;width:170px">
    <div style="font-size:22px;line-height:1.05">BLUE HARBOR<br>MORTGAGES</div>
    <div class="brand__tagline" style="font-size:6px">WE THINK OUTSIDE THE BOX</div>
  </div>

  <h1 class="headline" style="left:30px;top:276px;font-size:34px">
    <span class="headline__lead">We Think</span>
    <span class="headline__accent">Outside the Box</span>
  </h1>
  <div class="rule" style="left:30px;top:351px;width:318px"></div>
  <p class="pitch" style="left:29px;top:360px;font-size:21px">We Get <b>The Lowest Rates</b> and<br>Best Deals <b>For Our Clients</b></p>
  <div class="call" style="left:28px;top:422px;font-size:21px">Call Maren:</div>
  <div class="phone" style="left:28px;top:450px;font-size:32px">
    <svg width="22" height="22" viewBox="0 0 24 24"><path d="M6.6 10.8a15 15 0 0 0 6.6 6.6l2.2-2.2a1 1 0 0 1 1-.25 11.4 11.4 0 0 0 3.6.57 1 1 0 0 1 1 1V20a1 1 0 0 1-1 1A17 17 0 0 1 3 4a1 1 0 0 1 1-1h3.5a1 1 0 0 1 1 1c0 1.25.2 2.45.57 3.57a1 1 0 0 1-.25 1z" fill="#ffffff"/></svg>
    709-555-0142
  </div>
  <div class="cta" style="left:30px;top:514px;width:132px;height:28px;font-size:18px">Get Started<span>»</span></div>
  <div class="footer" style="top:560px;width:604px;height:44px;padding-left:28px;font-size:17px">
    <span class="footer__item"><i class="footer__icon" style="width:14px;height:14px"></i>www.<b>coveviewloans</b>.com</span>
    <span class="footer__sep">|</span>
    <span class="footer__item"><i class="footer__icon" style="width:14px;height:14px"></i>info@<b>coveviewloans</b>.com</span>
  </div>
</section>

<section class="post post--wide">
  <svg class="art" width="1073" height="602" viewBox="0 0 1073 602">
    <defs>
      <linearGradient id="wd-scene" x1="0" y1="0" x2="0" y2="1">
        <stop offset="0" stop-color="#3f7fd8"/><stop offset=".3" stop-color="#8a8a6e"/><stop offset="1" stop-color="#4f8a36"/>
      </linearGradient>
      <linearGradient id="wd-person" x1="0" y1="0" x2="0" y2="1">
        <stop offset="0" stop-color="#c99563"/><stop offset=".5" stop-color="#d8a37a"/><stop offset=".62" stop-color="#16204a"/><stop offset="1" stop-color="#101a40"/>
      </linearGradient>
      <linearGradient id="wd-house" x1="0" y1="0" x2="1" y2="1">
        <stop offset="0" stop-color="#eef0f2"/><stop offset="1" stop-color="#c7a58c"/>
      </linearGradient>
    </defs>
    <path role="img" aria-label="Hillside of colourful houses under blue sky in St. John's" d="M372,0 L1073,0 L1073,230 Q930,300 840,345 Q760,380 710,330 L470,180 Q390,120 372,0 Z" fill="url(#wd-scene)"/>
    <path d="M0,0 L372,0 Q378,105 405,142 L235,232 Q200,250 165,232 L0,145 Z" fill="#ff4100"/>
    <polygon points="606,155 709,212 709,328 606,385 504,328 504,212" fill="#b8c4de" opacity=".6"/>
    <polygon role="img" aria-label="Hands holding a small model house and keys" points="606,164 700,217 700,323 606,376 512,323 512,217" fill="url(#wd-house)"/>
    <path role="img" aria-label="Portrait of the mortgage broker" d="M764,602 Q764,400 830,290 Q880,145 960,145 Q1040,150 1060,260 Q1073,300 1073,340 L1073,602 Z" fill="url(#wd-person)"/>
  </svg>

  <div class="brand" style="left:55px;top:60px;width:265px">
    <div style="font-size:30px;line-height:1.05">BLUE HARBOR<br>MORTGAGES</div>
    <div class="brand__tagline" style="font-size:9px">WE THINK OUTSIDE THE BOX</div>
  </div>

  <h1 class="headline" style="left:52px;top:256px;font-size:44px">
    <span class="headline__lead">We Think</span>
    <span class="headline__accent">Outside the Box</span>
  </h1>
  <div class="rule" style="left:54px;top:354px;width:406px"></div>
  <p class="pitch" style="left:51px;top:366px;font-size:29px">We Get <b>The Lowest Rates</b> and<br>Best Deals <b>For Our Clients</b></p>
  <div class="call" style="left:49px;top:444px;font-size:29px">Call Maren:</div>
  <div class="phone" style="left:49px;top:480px;font-size:42px">
    <svg width="28" height="28" viewBox="0 0 24 24"><path d="M6.6 10.8a15 15 0 0 0 6.6 6.6l2.2-2.2a1 1 0 0 1 1-.25 11.4 11.4 0 0 0 3.6.57 1 1 0 0 1 1 1V20a1 1 0 0 1-1 1A17 17 0 0 1 3 4a1 1 0 0 1 1-1h3.5a1 1 0 0 1 1 1c0 1.25.2 2.45.57 3.57a1 1 0 0 1-.25 1z" fill="#ffffff"/></svg>
    709-555-0142
  </div>
  <div class="cta" style="left:512px;top:480px;width:182px;height:38px;font-size:25px">Get Started<span>»</span></div>
  <div class="footer" style="top:542px;width:766px;height:60px;padding-left:50px;font-size:22px">
    <span class="footer__item"><i class="footer__icon" style="width:18px;height:18px"></i>www.<b>coveviewloans</b>.com</span>
    <span class="footer__sep">|</span>
    <span class="footer__item"><i class="footer__icon" style="width:18px;height:18px"></i>info@<b>coveviewloans</b>.com</span>
  </div>
</section>

<div class="caption" style="left:113px;top:628px;width:344px">Instagram post 1080 x 1080</div>
<div class="caption" style="left:507px;top:631px;width:611px">Instagram post 1080 x 608</div>

</body>
</html>
```